Industry / Entity Type

Financial consultancy / advisers

Current site is: http://www.brightmoor-counsel.com

Looking for a complete overhaul of this site, we are after a clean modern look. Will require the ability to easily add, update and remove content, hence the WordPress design.
Example:
Add case studies
Industry documentation (downloadable brochures / flyers and such)

What we like from our current site is the colour the fonts and the logo (the city of London) we would like to have other city outlines (NYC and Tokyo, Hong Kong, Singapore).

The site will be used by our potential clients to get in contact and re-view the case studies, if possible would like to have a client login area where they can download our documents like NDA’s etc and T&C’s.

Task Outline

Create a Web Design (Coded - Design and coding required)
Designer must provide full implementation/coding depending on the platform chosen by the client (i.e. WordPress theme, HTML/CSS, bootstrap etc.)

Task Description

I need a full website built that must work on desktop and mobile. I can provide the London city skyline and the font file, which we have used. Some stock industrial photos will be required.

Requirements:

*Splash page
*What We Do
*How We do it
*Who Are We? To have the same information and links as the current site
*Why use us?
*Clients: To have the same information and links as the current site
*Partners: To have the same information and links as the current site
*Contact:

Target Market(s)

Financial institutions trading Equities, Futures, Options, Forex and Fixed Income.
Regulators, Exchanges, ECN’s
Buy side firms and Sell side firms

Industry/Entity Type

Financial

Coding

Coded - Design and coding required

Number of Pages Required

5+ page

Font styles to use
Sans Serif

Colors
f04a50

Requirements
Must have
• Splash page
• What We Do
• How We do it
• Who Are We? To have the same information and links as the current site
• Why use us?
• Clients: To have the same information and links as the current site
• Partners: To have the same information and links as the current site
• Contact:

```html
<!DOCTYPE html>
<html lang="en">
<head>
<meta charset="utf-8">
<title>Brightmoor Counsel</title>
<link href="https://fonts.googleapis.com/css2?family=Michroma&family=Maven+Pro:wght@400;500;600&display=swap" rel="stylesheet">
<style>
:root{
  --accent:#f04a50;
  --ink:#222428;
  --text:#6b6b6b;
  --muted:#8a8a8a;
  --panel:#f3f3f3;
  --rule:#d9d9d9;
  --white:#ffffff;
  --display:"Michroma", sans-serif;
  --body:"Maven Pro", sans-serif;
}
*{margin:0;padding:0;box-sizing:border-box}
html,body{width:1200px;height:2258px;overflow:hidden;background:var(--white)}
body{position:relative;font-family:var(--body);color:var(--text)}
.abs{position:absolute}

/* hero */
.hero{left:0;top:0;width:1200px;height:550px;
  background:linear-gradient(180deg,#1c2633 0%,#3a4656 30%,#6b5a55 52%,#3b4350 70%,#5d6a75 85%,#3a434c 100%)}
.site-header{left:0;top:0;width:1200px;height:100px;border-bottom:1px solid rgba(255,255,255,.25)}
.brand{left:95px;top:34px;display:flex;align-items:center;gap:10px;color:var(--white);font-family:var(--body);font-weight:500;font-size:17px;letter-spacing:3px}
.brand .mark{width:12px;height:12px;background:var(--white)}
.main-nav{right:96px;top:40px;display:flex;gap:21px;font-size:15px;color:var(--white)}
.main-nav .current{color:var(--accent)}
.hero-title{left:0;width:1200px;top:208px;text-align:center;font-family:var(--display);font-size:40px;color:var(--white);letter-spacing:4px}
.hero-sub{left:0;width:1200px;top:290px;text-align:center;font-size:21px;color:var(--white);letter-spacing:1px}
.btn-solid{left:488px;top:355px;width:224px;height:45px;border-radius:23px;background:var(--accent);border:2px solid var(--white);color:var(--white);font-size:17px;font-weight:500;display:flex;align-items:center;justify-content:center;letter-spacing:.5px}
.dots{left:565px;top:479px;display:flex;gap:5px}
.dots span{width:14px;height:14px;border-radius:50%;border:2px solid var(--white)}
.dots .on{background:var(--white)}

/* welcome */
.section-title{font-family:var(--display);color:var(--ink);font-size:26px}
.welcome-title{left:0;width:1200px;top:604px;text-align:center}
.welcome-text{left:230px;width:740px;top:656px;text-align:center;font-size:13px;line-height:26px}
.service{width:264px;text-align:center}
.service svg{display:block;margin:0 auto}
.service h3{margin-top:46px;font-size:19px;font-weight:500;color:var(--ink);letter-spacing:.5px}
.service p{margin-top:10px;font-size:13px;line-height:21px}

/* how */
.how-panel{left:0;top:1047px;width:1200px;height:412px;background:var(--panel);border-top:1px solid #e2e2e2;border-bottom:1px solid #e2e2e2}
.how-photo{left:0;top:1047px;width:622px;height:412px;
  clip-path:polygon(0 0,100% 0,83% 100%,0 100%);
  background:radial-gradient(circle at 35% 45%,#d9a760 0%,#8a6a45 14%,#3c4656 36%,#2e3846 100%)}
.how-title{left:664px;top:1104px}
.how-text{left:664px;top:1160px;width:440px;font-size:13px;line-height:25px}
.how-text p+p{margin-top:24px}
.btn-outline{height:31px;border:1px solid #9a9a9a;border-radius:16px;color:var(--accent);font-size:12px;font-weight:600;display:flex;align-items:center;justify-content:center;letter-spacing:.5px}
.how-btn{left:664px;top:1362px;width:133px}

/* why */
.why-title{left:99px;top:1542px}
.why-list{left:99px;top:1600px;list-style:none}
.why-list li{display:flex;align-items:center;gap:12px;height:36.6px;font-size:13px}
.why-btn{left:99px;top:1800px;width:144px;height:36px;border-radius:18px}
.device{left:630px;top:1536px;width:522px;height:304px;
  background:linear-gradient(180deg,#1a1a1a 0%,#1a1a1a 91%,#c9c9c9 92%,#e8e8e8 97%,#bdbdbd 100%);
  border-radius:14px 14px 4px 4px}
.device-screen{left:695px;top:1556px;width:394px;height:258px;background:linear-gradient(180deg,#eef0f6,#dfe3ee)}

/* footer */
.footer-rule{left:0;top:1904px;width:1200px;height:4px;background:var(--accent)}
.footer-brand{left:78px;top:2026px;display:flex;align-items:center;gap:10px;color:var(--ink);font-weight:500;font-size:17px;letter-spacing:3px}
.footer-brand .mark{width:12px;height:12px;background:var(--ink)}
.footer-head{font-family:var(--display);font-size:15px;color:var(--ink)}
.footer-col{font-size:13px;line-height:19.6px}
.info-links{list-style:none;color:var(--text)}
.newsletter p{margin-top:20px;line-height:21px}
.email-field{margin-top:18px;width:253px;border-bottom:1px solid var(--rule);padding:0 0 10px 14px;color:#9a9a9a;font-size:12px}
.btn-sub{margin-top:20px;width:95px;height:30px;border-radius:15px;font-weight:400;font-size:12px}
.contact-row{display:flex;gap:18px;align-items:flex-start;font-size:13px;line-height:21px}
.contact-row svg{flex:none;margin-top:4px}
.footer-divider{left:99px;top:2182px;width:1003px;height:1px;background:var(--rule)}
.copyright{left:99px;top:2214px;font-size:12px}
.social{left:976px;top:2209px;display:flex;gap:7px}
.social span{width:27px;height:27px;border-radius:50%;border:1px solid var(--accent);display:flex;align-items:center;justify-content:center}
.social span i{width:8px;height:8px;border-radius:50%;background:var(--accent)}
</style>
</head>
<body>

<!-- Hero -->
<div class="abs hero" role="img" aria-label="City skyline with a suspension bridge over the river at dusk"></div>
<header class="abs site-header">
  <div class="abs brand"><span class="mark"></span>BRIGHTMOOR COUNSEL</div>
  <nav class="abs main-nav">
    <span class="current">Home</span><span>What we do</span><span>How we do it</span><span>Who are we</span><span>Why use us</span><span>Clients</span><span>Partners</span><span>Contact</span>
    <svg width="14" height="14" viewBox="0 0 14 14" style="margin-top:2px"><circle cx="5.5" cy="5.5" r="4" fill="none" stroke="#fff" stroke-width="2"/><line x1="8.5" y1="8.5" x2="12.5" y2="12.5" stroke="#fff" stroke-width="2.4" stroke-linecap="round"/></svg>
  </nav>
</header>
<h1 class="abs hero-title">Genuine Motivation</h1>
<p class="abs hero-sub">TO SEE OUR CLIENTS SUCCEED</p>
<div class="abs btn-solid">GET MORE INFO &gt;&gt;</div>
<div class="abs dots"><span class="on"></span><span></span><span></span><span></span></div>

<!-- Welcome -->
<h2 class="abs section-title welcome-title">Welcome to Brightmoor Counsel</h2>
<p class="abs welcome-text">Since founding Brightmoor Counsel in 2014 we have dedicated ourselves to the provision of services. What differentiates us from other advisers or consultancies is a genuine motivation to see our clients succeed.</p>

<div class="abs service" style="left:71px;top:752px">
  <svg width="110" height="108" viewBox="0 0 110 108">
    <rect x="42" y="2" width="66" height="90" fill="#f04a50"/>
    <rect x="56" y="18" width="40" height="5" fill="#fff"/><rect x="56" y="38" width="40" height="5" fill="#fff"/><rect x="56" y="58" width="40" height="5" fill="#fff"/><rect x="56" y="76" width="40" height="5" fill="#fff"/>
    <circle cx="24" cy="33" r="12" fill="none" stroke="#f04a50" stroke-width="8" stroke-dasharray="5 3.5"/>
    <circle cx="30" cy="78" r="19" fill="none" stroke="#fff" stroke-width="6"/>
    <circle cx="30" cy="78" r="15" fill="none" stroke="#f04a50" stroke-width="11" stroke-dasharray="6 4"/>
    <circle cx="30" cy="78" r="5" fill="#fff"/>
  </svg>
  <h3>Data Management</h3>
  <p>At vero eos et accusamus et iustodi dignissimos ducimus qui blan</p>
</div>
<div class="abs service" style="left:335px;top:752px">
  <svg width="108" height="108" viewBox="0 0 108 108">
    <circle cx="54" cy="54" r="44" fill="none" stroke="#f04a50" stroke-width="14" stroke-dasharray="60 4 60 4 60 4 34 500"/>
    <rect x="33" y="58" width="10" height="20" fill="#f04a50"/><rect x="49" y="46" width="10" height="32" fill="#f04a50"/><rect x="65" y="34" width="10" height="44" fill="#f04a50"/>
  </svg>
  <h3>Analytics</h3>
  <p>At vero eos et accusamus et iustodi dignissimos ducimus qui blan</p>
</div>
<div class="abs service" style="left:598px;top:752px">
  <svg width="116" height="108" viewBox="0 0 116 108">
    <ellipse cx="42" cy="52" rx="38" ry="30" fill="#f04a50"/><path d="M16 72 L6 96 L36 78 Z" fill="#f04a50"/>
    <ellipse cx="70" cy="40" rx="42" ry="32" fill="#f04a50" stroke="#fff" stroke-width="5"/><path d="M96 62 L110 90 L80 70 Z" fill="#f04a50"/>
    <circle cx="52" cy="40" r="6" fill="#fff"/><circle cx="70" cy="40" r="6" fill="#fff"/><circle cx="88" cy="40" r="6" fill="#fff"/>
  </svg>
  <h3>Consulting</h3>
  <p>At vero eos et accusamus et iustodi dignissimos ducimus qui blan</p>
</div>
<div class="abs service" style="left:862px;top:752px">
  <svg width="108" height="108" viewBox="0 0 108 108">
    <circle cx="54" cy="52" r="24" fill="#f04a50"/>
    <path d="M30 52 H78 M54 28 V76 M36 38 H72 M36 66 H72" stroke="#fff" stroke-width="2.5" fill="none"/>
    <ellipse cx="54" cy="52" rx="11" ry="24" fill="none" stroke="#fff" stroke-width="2.5"/>
    <ellipse cx="54" cy="54" rx="52" ry="20" fill="none" stroke="#f04a50" stroke-width="6" transform="rotate(45 54 54)"/>
    <ellipse cx="54" cy="54" rx="52" ry="20" fill="none" stroke="#f04a50" stroke-width="6" transform="rotate(-45 54 54)"/>
  </svg>
  <h3>Trading</h3>
  <p>At vero eos et accusamus et iustodi dignissimos ducimus qui blan</p>
</div>

<!-- How we do it -->
<div class="abs how-panel"></div>
<div class="abs how-photo" role="img" aria-label="Glowing light bulb filled with gears on a chalkboard of formulas"></div>
<h2 class="abs section-title how-title">How We Do It</h2>
<div class="abs how-text">
  <p>At vero eos et accusamus et iusto odio dignissimos ducimus qui blanditiis prasent ium voluptatum deleniti atque corrupti quo.</p>
  <p>Dolores et quas molestias excepturi sint occaecati cupiditate non provident similiq ue sunt in culpa qui officia deserunt mollitia animi, id est laborum et dolorum fug t harum quidem rerum facilis est et expedita voluptas assumen est, omnis dolorr epellend poribus autem quibusdam et aut officiis.</p>
</div>
<div class="abs btn-outline how-btn">READ MORE &gt;&gt;</div>

<!-- Why choose us -->
<h2 class="abs section-title why-title">Why Choose us</h2>
<ul class="abs why-list">
  <li><svg width="15" height="15" viewBox="0 0 15 15"><circle cx="7.5" cy="7.5" r="7.5" fill="#f04a50"/><path d="M4 7.7 L6.6 10.2 L11 5.3" stroke="#fff" stroke-width="2" fill="none"/></svg>At vero eos et accusamus et iusto odio dignissimos ducimus qui blaniis</li>
  <li><svg width="15" height="15" viewBox="0 0 15 15"><circle cx="7.5" cy="7.5" r="7.5" fill="#f04a50"/><path d="M4 7.7 L6.6 10.2 L11 5.3" stroke="#fff" stroke-width="2" fill="none"/></svg>Praesentium voluptatum deleniti atque corrupti quos dolores et quas</li>
  <li><svg width="15" height="15" viewBox="0 0 15 15"><circle cx="7.5" cy="7.5" r="7.5" fill="#f04a50"/><path d="M4 7.7 L6.6 10.2 L11 5.3" stroke="#fff" stroke-width="2" fill="none"/></svg>Excepturi sint occaecati cupiditate non provident, similiqt in culpa qui</li>
  <li><svg width="15" height="15" viewBox="0 0 15 15"><circle cx="7.5" cy="7.5" r="7.5" fill="#f04a50"/><path d="M4 7.7 L6.6 10.2 L11 5.3" stroke="#fff" stroke-width="2" fill="none"/></svg>Nam libero tempore, cum soluta nobis est eligendi optio</li>
  <li><svg width="15" height="15" viewBox="0 0 15 15"><circle cx="7.5" cy="7.5" r="7.5" fill="#f04a50"/><path d="M4 7.7 L6.6 10.2 L11 5.3" stroke="#fff" stroke-width="2" fill="none"/></svg>Dit quo minus id quod maxime placeat facere possimus, omnis volup</li>
</ul>
<div class="abs btn-outline why-btn">READ MORE &gt;&gt;</div>
<div class="abs device" role="img" aria-label="Laptop showing a candlestick trading chart"></div>
<div class="abs device-screen" role="img" aria-label="Candlestick trading chart on screen"></div>

<!-- Footer -->
<div class="abs footer-rule"></div>
<div class="abs footer-brand"><span class="mark"></span>BRIGHTMOOR COUNSEL</div>

<div class="abs footer-col" style="left:399px;top:1962px">
  <h4 class="footer-head">Information</h4>
  <ul class="info-links" style="margin-top:14px">
    <li>Home</li><li>What we do</li><li>How we do it</li><li>Who are we</li><li>Why use us</li><li>Clients</li><li>Partners</li><li>Contact</li>
  </ul>
</div>

<div class="abs footer-col newsletter" style="left:590px;top:1962px">
  <h4 class="footer-head">Newsletter Subscription</h4>
  <p>Register your Email Address to get<br>Information about us</p>
  <div class="email-field">Email Address</div>
  <div class="btn-outline btn-sub">SUBSCRIBE</div>
</div>

<div class="abs footer-col" style="left:914px;top:1962px">
  <h4 class="footer-head">Contact Us</h4>
  <div class="contact-row" style="margin-top:18px">
    <svg width="9" height="13" viewBox="0 0 9 13"><path d="M4.5 0 A4.5 4.5 0 0 1 9 4.5 C9 8 4.5 13 4.5 13 C4.5 13 0 8 0 4.5 A4.5 4.5 0 0 1 4.5 0Z" fill="#f04a50"/><circle cx="4.5" cy="4.5" r="1.7" fill="#fff"/></svg>
    <span>Suite 4 Alder Court, Fenwick Row,<br>Harlow Vale,<br>Essex, HV3 2QT</span>
  </div>
  <div class="contact-row" style="margin-top:21px">
    <svg width="11" height="11" viewBox="0 0 11 11"><path d="M2 0 L4 2.6 L2.8 4 C3.6 5.8 5.2 7.4 7 8.2 L8.4 7 L11 9 L9.4 11 C4.5 10.5 0.5 6.5 0 1.6 Z" fill="#f04a50"/></svg>
    <span>+1-555-014-2290</span>
  </div>
  <div class="contact-row" style="margin-top:20px">
    <svg width="12" height="10" viewBox="0 0 12 10"><rect width="12" height="10" rx="1" fill="#f04a50"/><path d="M0.5 1 L6 5.5 L11.5 1" stroke="#fff" stroke-width="1.3" fill="none"/></svg>
    <span>info@brightmoor-counsel.com</span>
  </div>
</div>

<div class="abs footer-divider"></div>
<p class="abs copyright">Copyrights © 2017, Brightmoor Counsel. All rights reserved.</p>
<div class="abs social"><span><i></i></span><span><i></i></span><span><i></i></span><span><i></i></span></div>

</body>
</html>
```